Real Estate stationery - need an interesting, eye catching design

I need a letterhead and #10 envelope design in the same theme.
I am looking for an interesting, eye catching design that would stand out in the crowd. I am in the real estate business(which is very competitive) in Florida so standing out and being different is very important to me.
Marguerite(Rita) Delacourt (name), RealtorĀ® (title), 352-608-2147 (cell), bayviewritahomes@quellmail.com (email), www.bayviewritahomes.com(website), 915 Calloway Creek Blvd.,Ste. 3140, Longwood, FL 32779 (business address)

```html
<!DOCTYPE html>
<html lang="en">
<head>
<meta charset="utf-8">
<title>Crestmoor Realty Stationery</title>
<link rel="stylesheet" href="https://fonts.googleapis.com/css2?family=Raleway:wght@400;500&family=Roboto:wght@400;500&display=swap">
<style>
  :root {
    --bg: #dedede;
    --paper: #fafafa;
    --bronze: #875d28;
    --slate: #858890;
    --ink: #4a4a4a;
    --ink-soft: #666666;
    --sign-fill: #e9e1d6;
  }
  * { margin: 0; padding: 0; box-sizing: border-box; }
  html, body { width: 1200px; height: 843px; overflow: hidden; background: var(--bg); }
  body { position: relative; font-family: "Raleway", sans-serif; color: var(--ink); }

  .sheet { position: absolute; background: var(--paper); }

  /* Letterhead */
  .letterhead { left: 74px; top: 61px; width: 508px; height: 715px; }
  .band { position: absolute; }
  .band--bronze { background: var(--bronze); }
  .band--slate { background: var(--slate); }
  .letterhead .band--bronze { left: 0; top: 53px; width: 232px; height: 28px; }
  .letterhead .band--slate { left: 232px; top: 59px; right: 0; height: 22px; }

  .brand { position: absolute; text-align: center; }
  .brand__name { font-family: "Raleway", sans-serif; font-weight: 500; color: var(--bronze); font-size: 15px; letter-spacing: 0.5px; display: flex; align-items: center; justify-content: center; gap: 6px; }
  .brand__mark { width: 8px; height: 8px; background: var(--bronze); display: inline-block; }
  .brand__tag { font-size: 5px; letter-spacing: 5px; color: var(--ink-soft); margin-top: 3px; }
  .letterhead .brand { left: 150px; width: 210px; top: 88px; }

  .letter { position: absolute; left: 44px; top: 200px; width: 422px; }
  .letter__salutation { font-size: 13px; line-height: 16px; margin-bottom: 26px; }
  .letter__body p { font-size: 7.6px; line-height: 11px; color: var(--ink-soft); margin-bottom: 11px; }
  .letter__closing { font-size: 7.6px; color: var(--ink-soft); margin-top: 20px; }
  .signature { position: absolute; left: 40px; top: 502px; width: 90px; height: 36px; background: var(--sign-fill); }

  .footer { position: absolute; left: 0; right: 0; top: 673px; text-align: center; font-family: "Roboto", sans-serif; font-size: 7px; line-height: 10px; color: var(--ink); }
  .footer__label { color: var(--bronze); font-weight: 500; }

  /* Envelope back */
  .envelope-back { left: 621px; top: 275px; width: 512px; height: 233px; overflow: hidden; }
  .envelope-back svg { position: absolute; left: 0; top: 0; }
  .envelope-back .brand { left: 0; right: 0; top: 30px; }
  .envelope-back .brand__name { font-size: 10px; color: var(--slate); }
  .envelope-back .brand__mark { width: 6px; height: 6px; background: var(--slate); }

  /* Envelope front */
  .envelope-front { left: 621px; top: 543px; width: 512px; height: 233px; }
  .envelope-front .band--bronze { left: 0; top: 19px; width: 90px; height: 25px; }
  .envelope-front .band--slate { left: 90px; top: 24px; right: 0; height: 20px; }
  .envelope-front .brand { left: 10px; width: 145px; top: 48px; }
  .envelope-front .brand__name { font-size: 11px; }
  .envelope-front .brand__tag { font-size: 4px; letter-spacing: 4px; }
  .return-address { position: absolute; left: 10px; width: 145px; top: 75px; text-align: center; font-family: "Roboto", sans-serif; font-size: 6.5px; line-height: 9px; color: var(--ink); }
</style>
</head>
<body>

<section class="sheet letterhead">
  <div class="band band--bronze"></div>
  <div class="band band--slate"></div>
  <div class="brand">
    <div class="brand__name"><span class="brand__mark"></span>Crestmoor Realty</div>
    <div class="brand__tag">REAL ESTATE</div>
  </div>

  <div class="letter">
    <p class="letter__salutation">Dear Mr. Hartley,</p>
    <div class="letter__body">
      <p>Lorem ipsum dolor sit amet, consectetur adipiscing elit. Donec orci purus, luctus vitae dignissim eu, iaculis sed purus. Vivamus faucibus, ipsum nec aliquet viverra, leo mauris condimentum ligula, sit amet sagittis enim ligula quis arcu. Nam egestas tortor id nisi porttitor mattis. In tortor ante, ultricies in suscipit a, tempus non massa. Vivamus et auctor mi. Fusce vel massa nulla. Phasellus nec eros mauris, et scelerisque orci.</p>
      <p>Donec malesuada orci vitae nulla accumsan porta a id massa. Quisque accumsan iaculis magna sit amet fringilla. Maecenas consequat, magna eget tincidunt semper, odio nibh rutrum mi, id feugiat ante nisi eu risus. Vestibulum nunc orci, rhoncus a placerat in, ultricies in mi. Cras mattis varius eros, vel fringilla nisi suscipit eget. Quisque scelerisque sagittis nulla at porttitor.</p>
      <p>Sed id augue vitae urna euismod commodo aliquet a quam. Pellentesque arcu velit, cursus et malesuada ut, consequat et diam. Nullam erat sem, rhoncus id ullamcorper vitae, rhoncus et arcu. In ultricies ultricies nulla, ut rutrum nisi iaculis at. Donec eu magna a metus ornare faucibus. Fusce aliquet faucibus ultricies. Morbi semper, est id tincidunt gravida, sem arcu adipiscing lacus, ac bibendum nulla leo eu purus. Quisque nec diam sed risus consectetur a accumsan quis quis nibh. Vestibulum id purus lorem.</p>
      <p>It is a long established fact that a reader will be distracted by the readable content of a page when looking at its layout. The point of using Lorem Ipsum is that it has a more-or-less normal distribution of letters, as opposed to using 'Content here, content here', making it look like readable English. Many desktop publishing packages</p>
    </div>
    <p class="letter__closing">Sincerely,</p>
  </div>
  <div class="signature" role="img" aria-label="Handwritten signature of Owen Hartley"></div>

  <div class="footer">
    <div>915 Calloway Creek Blvd., Ste. 3140, Ferndale Cove, FL 32905</div>
    <div><span class="footer__label">M:</span> 352-608-2147 &nbsp;<span class="footer__label">E:</span> bayviewritahomes@quellmail.com &nbsp;<span class="footer__label">W:</span> www.bayviewritahomes.com</div>
  </div>
</section>

<section class="sheet envelope-back">
  <svg width="512" height="233" viewBox="0 0 512 233" aria-hidden="true">
    <path d="M2 0 L8 50 Q12 72 40 72 L472 72 Q500 72 504 50 L510 0" fill="none" stroke="#e6e6e6" stroke-width="1.5"/>
  </svg>
  <div class="brand">
    <div class="brand__name"><span class="brand__mark"></span>Crestmoor Realty</div>
  </div>
</section>

<section class="sheet envelope-front">
  <div class="band band--bronze"></div>
  <div class="band band--slate"></div>
  <div class="brand">
    <div class="brand__name"><span class="brand__mark"></span>Crestmoor Realty</div>
    <div class="brand__tag">REAL ESTATE</div>
  </div>
  <div class="return-address">
    915 Calloway Creek Blvd., Ste. 3140,<br>Ferndale Cove, FL 32905
  </div>
</section>

</body>
</html>
```